Brochure design

I have attached our current prospectus which has been created by ourselves, we are looking for this now to be professionally designed. We are happy to use the content but also for this to be amended to co-incide with the message on our website www.tumblewick.co.uk and for it to be condensed into a more reader friendly format. Whilst we are happy with this website, again it was created by ourselves and we are not necessarily following the same design features but the colour scheme should be similar to the website. The prospectus will be printed on 2 x A4 sheets folded to make an 8 page A5 booklet with page 1 being a front cover and page 8 being back cover with contact information. The business is a childrens day nursery so the prospectus should be bright, fun, to the point and informative. I am happy to provide any further information to designers who may be looking at this by emailing me dana@tumblewick.co.uk . The completed product should allow us to edit the text for example to communicate price changes.

Further information:

Tumblewick Nursery is very unique compared with other Nurseries. Most nurseries segregate age groups into different rooms whereas at Tumblewick aged groups mix together to create a homely environment and also children are not moving through different rooms every year. Could we therefore get a message through the prospectus which reflects this, we currently use a strapline "A unique home from home childcare experience" but we are looking to change this and will be grateful for ideas.

We have no preference whether stock images are used or our own, However, stock images and ours should not be included on the same page.

From the designs received we do like stock images for the front and back cover but these must be relevant, ie showing children aged 3 months old to 5 years old.

Target Market(s)

Mum's mainly but Dad's also of children aged 0 to 5 years old. Age range of parents between 22 and 45.

Industry/Entity Type

Environment

Font styles to use
Serif

Colors
acd036
b768aa
e9f1ce
ecdaeb
ceeae6

Requirements
Must have
• Fun, Colorfull, Bright, Concise, Informative.
Should not have
• Stock images and supplied images on the same pages

```html
<!DOCTYPE html>
<html lang="en">
<head>
<meta charset="utf-8">
<title>Tumblewick Nursery – Our Nursery</title>
<link href="https://fonts.googleapis.com/css2?family=Jost:wght@400;500&family=Lobster+Two:wght@400;700&display=swap" rel="stylesheet">
<style>
:root{
  --purple:#b2579f;
  --green:#acd036;
  --green-soft:#e9f1ce;
  --pink-soft:#ecdaeb;
  --aqua-soft:#ceeae6;
  --ink:#1d1d1b;
  --paper:#ffffff;
}
*{margin:0;padding:0;box-sizing:border-box}
html,body{width:1200px;height:825px;overflow:hidden;background:var(--paper)}
.spread{position:relative;width:1200px;height:825px;overflow:hidden;background:
  radial-gradient(ellipse 420px 260px at 960px 520px,rgba(233,241,206,.7),transparent 70%),var(--paper);
  font-family:"Jost",sans-serif;color:var(--ink)}
.edge{position:absolute;top:0;height:825px;width:56px;
  background:repeating-linear-gradient(180deg,var(--green-soft) 0 11px,var(--pink-soft) 11px 22px,var(--aqua-soft) 22px 33px,var(--green) 33px 44px)}
.edge--left{left:0}
.edge--right{right:0}
.photo{position:absolute}
.photo--artwork{left:55px;top:0;width:549px;height:296px;
  background:linear-gradient(135deg,#e6d84a 0%,#5ba5d8 40%,#2b2b2b 55%,#9ad0e8 75%,#d9e36a 100%)}
.photo--child{left:472px;top:424px;width:320px;height:401px;
  background:linear-gradient(180deg,#f6dcc4 0%,#f1c9a8 20%,#d6589f 50%,#1f6fc2 75%,#1a4f9a 100%);
  clip-path:polygon(58px 56px,88px 42px,168px 38px,193px 61px,228px 101px,243px 141px,246px 181px,228px 216px,198px 244px,158px 268px,140px 294px,320px 294px,320px 401px,0 401px,0 150px,28px 120px)}
.body{font-size:16.5px;line-height:20.8px;letter-spacing:.15px}
.body .line{display:block;white-space:nowrap;text-align:justify;text-align-last:justify}
.body .line--end{display:block;white-space:nowrap}
.intro{position:absolute;left:77px;top:302px;width:491px}
.heading{font-family:"Lobster Two",serif;font-weight:400;color:var(--purple);line-height:1.2}
.heading--nursery{position:absolute;left:77px;top:474px;font-size:40px}
.rooms-lead{position:absolute;left:77px;top:536px;font-family:"Lobster Two",serif;color:var(--purple);font-size:19px;line-height:22px;white-space:nowrap}
.rooms-text{position:absolute;left:77px;top:602px;width:350px}
.care-text{position:absolute;left:626px;top:14px;width:493px}
.heading--meals{position:absolute;left:626px;top:144px;font-size:42px;line-height:48px}
.meals-text{position:absolute;left:626px;top:246px;width:493px}
.menu{position:absolute;list-style:none;font-family:"Lobster Two",serif;color:var(--purple);font-size:19px}
.menu li{position:absolute;white-space:nowrap}
.menu li::before{content:"";position:absolute;left:-36px;top:5px;width:10px;height:10px;border-radius:50%;background:var(--green)}
.mealtime{position:absolute;left:626px;top:612px;width:493px}
</style>
</head>
<body>
<main class="spread">
  <div class="edge edge--left" role="img" aria-label="Column of pastel green, pink and aqua squares"></div>
  <div class="edge edge--right" role="img" aria-label="Column of pastel green, pink and aqua squares"></div>

  <div class="photo photo--artwork" role="img" aria-label="Children's painted and glittered artwork displayed on a nursery wall"></div>

  <p class="body intro">
    <span class="line">These ideas and interests will be displayed around he nursery all</span>
    <span class="line">of the time, as well as shared with the families at the nursery</span>
    <span class="line">through discussion with the key person and through email. You</span>
    <span class="line">can see all of our planning of activities and resources in the</span>
    <span class="line">hallway, along with each child’s individual next steps, which are</span>
    <span class="line">on display so that you see the process in which your child</span>
    <span class="line">influences the activities and resources available within the</span>
    <span class="line--end">nursery</span>
  </p>

  <h2 class="heading heading--nursery">Our Nursery</h2>
  <p class="rooms-lead">We have 3 children’s rooms in the nursery; these<br>are the Little Room, Green Room and Big Room.<br>At Tumblewick,</p>
  <p class="body rooms-text">
    <span class="line" style="width:350px">we name our rooms purely to ensure that</span>
    <span class="line" style="width:345px">each child has an age appropriate area with</span>
    <span class="line" style="width:345px">resources available to them however we aim</span>
    <span class="line" style="width:345px">to create an environment in which the</span>
    <span class="line" style="width:350px">children can explore and find various other</span>
    <span class="line" style="width:350px">activities that are available to them in each</span>
    <span class="line" style="width:316px">room.Each room is set up to provide an</span>
    <span class="line" style="width:294px">accessible environment for children to</span>
    <span class="line" style="width:268px">access resources which will enrich</span>
    <span class="line" style="width:240px">their creative, language,</span>
  </p>

  <div class="photo photo--child" role="img" aria-label="Toddler in a pink top holding a toy and a spade beside a blue water tray"></div>

  <p class="body care-text">
    <span class="line">mathematical, physical and social development whilst letting</span>
    <span class="line">them extend their knowledge about the world. They will have the</span>
    <span class="line">opportunity to play, have fun or be quiet and snuggle in with a</span>
    <span class="line">book depending on their mood. We aim to ensure that every</span>
    <span class="line">aspect of your child’s care, learning and development is catered</span>
    <span class="line--end">for.</span>
  </p>

  <h2 class="heading heading--meals">Freshly prepared for<br>your child..</h2>
  <p class="body meals-text">
    <span class="line">All of the nursery meals are prepared on site, fresh on the day</span>
    <span class="line">and planned to ensure that your child has a healthy and varied</span>
    <span class="line">diet. We use a 4 week menu system which we change every 3-4</span>
    <span class="line">months to ensure that the children have the opportunity to try</span>
    <span class="line">new things, as well as old favourites. All the meals are included</span>
    <span class="line--end">in the price of the fees, each day the nursery provides:</span>
  </p>

  <ul class="menu">
    <li style="left:712px;top:386px">Breakfast, of fresh fruit with cereal or toast</li>
    <li style="left:712px;top:426px">Snack, of fresh fruit or a healthy alternative</li>
    <li style="left:712px;top:466px">Lunch, a freshly prepared 2 course meal</li>
    <li style="left:838px;top:506px">Afternoon snack of fresh fruit or a<br><span style="display:block;margin-top:18px">healthy alternative</span></li>
    <li style="left:797px;top:586px">Tea, a lighter, 2 course meal</li>
  </ul>

  <div class="body mealtime">
    <span class="line" style="margin-left:108px">We try to ensure that all meal times are a time</span>
    <span class="line" style="margin-left:103px">where children can connect with the staff team and</span>
    <span class="line" style="margin-left:93px">are encouraged to create a sociable environment.</span>
    <span class="line" style="margin-left:74px">The lunchtime routine is staggered, where children can</span>
    <span class="line">choose when they are ready to eat and are encouraged to set</span>
    <span class="line" style="margin-left:176px">their place, wash their hands and sit and</span>
    <span class="line" style="margin-left:176px">eat with the staff team, as well as their</span>
    <span class="line" style="margin-left:176px">friends so that table manners can be</span>
    <span class="line--end" style="margin-left:176px">encouraged.</span>
  </div>
</main>
</body>
</html>
```